Redesign of business card for Cedar Ridge Mechanical

We are looking for a new design for our business cards for Cedar Ridge Mechanical. We are a plumbing & HVAC construction company, operating on the West Coast of Canada and USA. Logo attached.
Industry/Entity Type
Construction - Plumbing & HVAC
Contact Information for Business Card
Name, address, phone numbers, email, website address
Look and feel
Each slider illustrates characteristics of the customer's brand and the style your logo design should communicate.

```html
<!DOCTYPE html>
<html lang="en">
<head>
<meta charset="utf-8">
<title>Cedar Ridge Mechanical – Business Card</title>
<link href="https://fonts.googleapis.com/css2?family=Oswald:wght@600&family=Lato:wght@400&display=swap" rel="stylesheet">
<style>
  :root {
    --stage: #3a3a3a;
    --ink: #111111;
    --paper: #ffffff;
    --muted: #8a8a8a;
  }
  * { box-sizing: border-box; margin: 0; padding: 0; }
  html, body { width: 1200px; height: 895px; overflow: hidden; }
  body { background: var(--stage); position: relative; font-family: "Lato", sans-serif; }

  .card {
    position: absolute;
    width: 560px;
    height: 320px;
    border-radius: 18px;
    overflow: hidden;
  }
  .card--back { left: 60px; top: 90px; background: var(--ink); }
  .card--front { left: 580px; top: 480px; background: var(--paper); color: var(--ink); }

  .wordmark {
    position: absolute;
    display: flex;
    align-items: center;
    gap: 12px;
    font-family: "Oswald", sans-serif;
    font-weight: 600;
    text-transform: uppercase;
    letter-spacing: 1px;
    white-space: nowrap;
  }
  .wordmark__square { display: block; flex: none; }
  .card--back .wordmark { left: 0; right: 0; top: 130px; justify-content: center; font-size: 34px; color: var(--paper); }
  .card--back .wordmark__square { width: 30px; height: 30px; border: 4px solid var(--paper); }
  .card--front .wordmark { left: 0; right: 0; top: 40px; justify-content: center; font-size: 28px; color: var(--ink); }
  .card--front .wordmark__square { width: 24px; height: 24px; border: 4px solid var(--ink); }

  .identity {
    position: absolute;
    right: 320px;
    top: 150px;
    text-align: right;
  }
  .identity__name { font-family: "Oswald", sans-serif; font-weight: 600; font-size: 22px; letter-spacing: 0.5px; text-transform: uppercase; line-height: 1.2; }
  .identity__title { font-size: 16px; line-height: 1.3; }

  .divider { position: absolute; left: 256px; top: 140px; width: 1.5px; height: 70px; background: var(--ink); }

  .contacts { position: absolute; left: 272px; top: 140px; list-style: none; }
  .contacts li { display: flex; align-items: center; gap: 8px; font-size: 14.5px; line-height: 23px; }
  .contacts svg { width: 13px; height: 13px; flex: none; fill: var(--ink); }

  .address-band { position: absolute; left: 0; right: 0; top: 236px; height: 26px; }
  .address-band__block { position: absolute; top: 0; height: 26px; background: var(--ink); }
  .address-band__block--left { left: 0; width: 96px; }
  .address-band__block--right { right: 0; width: 34px; }
  .address-band__main {
    position: absolute; left: 104px; right: 42px; top: 0; height: 26px;
    background: var(--ink); color: var(--paper);
    font-size: 14px; line-height: 26px; text-align: center; letter-spacing: 0.3px;
  }
</style>
</head>
<body>

<section class="card card--back" aria-label="Card back">
  <div class="wordmark"><span class="wordmark__square"></span>Cedar Ridge Mechanical</div>
</section>

<section class="card card--front" aria-label="Card front">
  <div class="wordmark"><span class="wordmark__square"></span>Cedar Ridge Mechanical</div>

  <div class="identity">
    <p class="identity__name">Daniel Reyes Hart</p>
    <p class="identity__title">Founder and CEO</p>
  </div>

  <span class="divider"></span>

  <ul class="contacts">
    <li>
      <svg viewBox="0 0 16 16" aria-hidden="true"><path d="M3.6 1.2 6 3.6 4.6 5.4c.9 2 2.9 4 5 5l1.8-1.4 2.4 2.4-1.6 2.6C6.6 13.6 2.4 9.4 1 3.8z"/></svg>
      604-555-0182
    </li>
    <li>
      <svg viewBox="0 0 16 16" aria-hidden="true"><path d="M1 3h14v10H1zM2 4v.6l6 4.2 6-4.2V4z"/></svg>
      dhart@cedarridgemech.com
    </li>
    <li>
      <svg viewBox="0 0 16 16" aria-hidden="true"><path d="M8 1a7 7 0 1 0 0 14A7 7 0 0 0 8 1zm0 1.4c.8.8 1.5 2.2 1.7 3.8H6.3C6.5 4.6 7.2 3.2 8 2.4zM2.5 7.2h2.4c0 .6 0 1.1.1 1.6H2.5a5.6 5.6 0 0 1 0-1.6zm3.8 1.6V7.2h3.4v1.6zm4.8-1.6h2.4a5.6 5.6 0 0 1 0 1.6h-2.4zM8 13.6c-.8-.8-1.5-2.2-1.7-3.6h3.4c-.2 1.4-.9 2.8-1.7 3.6z"/></svg>
      www.cedarridgemech.com
    </li>
  </ul>

  <div class="address-band">
    <span class="address-band__block address-band__block--left"></span>
    <p class="address-band__main">4120 Harbor Lane, Suite 200, Portland, OR 97205</p>
    <span class="address-band__block address-band__block--right"></span>
  </div>
</section>

</body>
</html>
```